Luxury travel agency needs a website design

We are a travel agency specializing in booking luxury vacations. We specialize in Hawaii, Europe and Caribbean, but will do all vacations. I want a very classy website design which would attract luxury clients. The company name is "Harbors and Hammocks Travel Agency". Would love the web design to go with the color scheme of the logo. Hex codes included in files. Logo is attached. Would also love more Grey in the website. I want it very elegant

Coding

Coded - Design and coding required

Font styles to use
Sans Serif
Decorative

Requirements
Must have
• - Consultation Tab or a page where the client can fill out a short form about what vacation that they would want to book. I want this info to be sent to me in order for me to contact them.
- Somewhere with my contact info "email: marla@harborsandhammockstravel.example and phone number"
- Social media links
- About section "Marla Dunbevy - Agency Owner (picture provided)
Marla has been traveling full time for the passed two years and has been very passionate about travel from a young age. Marla is dedicated to working closely with clients to book their dream vacation.
Marla's specializations include honeymoons and anniversaries focusing on travel in Europe, Hawaii and all inclusive resorts in the Caribbean.

```html
<!DOCTYPE html>
<html lang="en">
<head>
<meta charset="utf-8">
<title>Harbors and Hammocks Travel Agency</title>
<link href="https://fonts.googleapis.com/css2?family=Montserrat:wght@300;400;600;700&family=Open+Sans:ital,wght@0,400;0,600;1,400&display=swap" rel="stylesheet">
<style>
:root{
  --gold:#f0c64b;
  --black:#0b0b0b;
  --ink:#222222;
  --grey:#6b6b6b;
  --light-grey:#ececec;
  --white:#ffffff;
}
*{box-sizing:border-box;margin:0;padding:0}
html,body{width:1200px;height:4476px;overflow:hidden}
body{font-family:"Open Sans",Arial,sans-serif;color:var(--ink);background:var(--white);position:relative}
.heading{font-family:"Montserrat",Arial,sans-serif;font-weight:700;text-transform:uppercase;letter-spacing:2px}
.ghost{position:absolute;left:0;right:0;text-align:center;font-family:"Montserrat",Arial,sans-serif;font-weight:700;text-transform:uppercase;font-size:78px;letter-spacing:4px;color:var(--light-grey);z-index:0}
.photo{position:absolute}

/* header */
.site-header{position:absolute;top:0;left:0;width:1200px;height:88px;background:rgba(0,0,0,.85);z-index:5;display:flex;align-items:center;padding:0 40px}
.brand{display:flex;align-items:center;gap:10px;font-family:"Montserrat",Arial,sans-serif;font-weight:600;color:var(--white);font-size:15px;letter-spacing:1px}
.brand-dot{width:26px;height:26px;border-radius:50%;background:var(--gold)}
.main-nav{margin-left:auto;display:flex;gap:36px;font-family:"Montserrat",Arial,sans-serif;font-size:13px;color:var(--white);text-transform:uppercase;letter-spacing:1px}
.main-nav .active{border-bottom:2px solid var(--gold);padding-bottom:4px}

/* hero */
.hero{position:absolute;top:0;left:0;width:1200px;height:680px}
.hero .photo{inset:0;background:linear-gradient(180deg,#6fa6d6 0%,#9cc6e4 35%,#2c93b4 62%,#1f6d6f 100%)}
.hero-title{position:absolute;top:310px;left:0;right:0;text-align:center;color:var(--white);font-size:52px;line-height:62px;letter-spacing:4px}

/* occasions */
.occasions{position:absolute;top:680px;left:0;width:1200px;height:540px}
.occasion{position:absolute;top:0;height:540px;width:1200px}
.occasion.honeymoon{clip-path:polygon(0 0,620px 0,560px 540px,0 540px);background:linear-gradient(160deg,#7db3c8,#c9a27a 60%,#8a6a4a)}
.occasion.anniversary{clip-path:polygon(628px 0,1200px 0,1200px 540px,568px 540px);background:linear-gradient(200deg,#8fbfdc,#c8d9e2 50%,#6e8f6a)}
.occasion-label{position:absolute;top:250px;width:600px;text-align:center;color:var(--white)}
.occasion-label .heading{font-size:36px;letter-spacing:3px}
.occasion-label .sub{font-family:"Montserrat",Arial,sans-serif;font-size:12px;letter-spacing:3px;margin-top:6px}
.occasion-label .ghost-word{position:absolute;left:0;right:0;top:-14px;font-size:58px;color:rgba(255,255,255,.25);font-family:"Montserrat",Arial,sans-serif;font-weight:700;letter-spacing:4px}

/* welcome */
.welcome{position:absolute;top:1220px;left:0;width:1200px;height:580px;text-align:center}
.welcome .ghost{top:40px}
.welcome h2{position:relative;z-index:1;margin-top:96px;font-size:36px;line-height:46px}
.welcome .tagline{margin-top:26px;font-family:"Montserrat",Arial,sans-serif;font-weight:600;font-size:16px;letter-spacing:2px}
.welcome p{width:880px;margin:30px auto 0;font-size:13px;line-height:30px;text-transform:uppercase;color:var(--grey);letter-spacing:.5px}
.btn{display:inline-block;background:var(--gold);color:var(--black);font-family:"Montserrat",Arial,sans-serif;font-weight:600;font-size:12px;text-transform:uppercase;letter-spacing:1px;padding:14px 28px}
.welcome .btn{margin-top:44px}

/* specialties */
.specialties{position:absolute;top:1800px;left:0;width:1200px;height:512px;background:linear-gradient(180deg,#294a55,#1b3a3f 55%,#0f2a2d)}
.specialties .ghost{top:50px;color:rgba(255,255,255,.12)}
.specialties h2{position:absolute;top:80px;left:0;right:0;text-align:center;color:var(--white);font-size:36px}
.spec-card{position:absolute;top:158px;width:332px;height:228px}
.spec-card .label{position:absolute;top:244px;left:0;right:0;text-align:center;color:var(--white);font-family:"Montserrat",Arial,sans-serif;font-weight:600;font-size:16px;letter-spacing:3px}
.spec-card .pin{position:absolute;left:152px;top:100px}

/* about */
.about{position:absolute;top:2400px;left:0;width:1200px;height:470px}
.about .portrait{left:88px;top:8px;width:500px;height:440px;background:linear-gradient(160deg,#7c6a55,#b99a82 50%,#6f5d4c)}
.about .ghost{left:640px;right:auto;top:44px;font-size:72px}
.about-text{position:absolute;left:668px;top:60px;width:470px;z-index:1}
.about-text h2{font-size:36px}
.about-text .name{margin-top:14px;font-family:"Montserrat",Arial,sans-serif;font-weight:600;font-size:14px;letter-spacing:2px;text-transform:uppercase}
.about-text .role{margin-top:16px;font-style:italic;font-size:14px;color:var(--grey)}
.about-text p{margin-top:30px;font-size:12px;line-height:26px;text-transform:uppercase;color:var(--grey)}

/* gallery */
.gallery{position:absolute;top:2900px;left:0;width:1200px;height:720px;text-align:center}
.gallery .ghost{top:6px}
.gallery h2{position:relative;z-index:1;margin-top:36px;font-size:36px}
.gallery-grid{position:absolute;top:98px;left:148px;display:grid;grid-template-columns:repeat(3,296px);grid-template-rows:repeat(2,262px);gap:18px 18px}
.gallery-grid div{position:relative}
.gallery .btn{position:absolute;top:660px;left:562px;padding:12px 30px}

/* contact */
.contact{position:absolute;top:3700px;left:0;width:1200px;height:580px}
.contact .desk{position:absolute;inset:0;background:linear-gradient(135deg,#d9d9d6,#f3f3f1 50%,#b9c3c8)}
.contact .panel{position:absolute;inset:0;background:var(--gold);clip-path:polygon(0 0,560px 0,660px 580px,0 580px)}
.contact .ghost{left:70px;right:auto;top:70px;text-align:left;color:rgba(255,255,255,.35);font-size:64px}
.contact h2{position:absolute;left:88px;top:90px;font-size:32px;color:var(--white)}
.contact-form{position:absolute;left:88px;top:160px;width:480px}
.field{background:var(--white);height:40px;font-size:13px;color:#999;padding:11px 12px;margin-bottom:12px}
.row{display:flex;gap:12px}
.row .field{flex:1}
.field.tall{height:82px}
.submit{background:var(--black);color:var(--white);text-align:center;font-family:"Montserrat",Arial,sans-serif;font-size:12px;font-weight:600;letter-spacing:1px;padding:13px 0}

/* footer */
.site-footer{position:absolute;top:4280px;left:0;width:1200px;height:196px;background:var(--black);color:var(--white);text-align:center}
.site-footer .brand{justify-content:center;margin-top:26px}
.contact-line{margin-top:18px;font-size:13px}
.socials{display:flex;justify-content:center;gap:18px;margin-top:16px}
.socials span{width:18px;height:18px;border-radius:50%;background:var(--white)}
.copyright{position:absolute;bottom:0;left:0;right:0;border-top:1px solid #333;font-size:11px;color:#aaa;padding:10px 0}
</style>
</head>
<body>

<header class="site-header">
  <div class="brand"><span class="brand-dot"></span>Harbors and Hammocks</div>
  <nav class="main-nav">
    <span class="active">Home</span><span>About Us</span><span>Packages</span><span>Consultation</span><span>Book Online</span><span>More</span><span>EN</span>
  </nav>
</header>

<section class="hero">
  <div class="photo" role="img" aria-label="Tropical beach with turquoise sea and palm leaves"></div>
  <h1 class="hero-title heading">Harbors and Hammocks<br>Travel Agency</h1>
</section>

<section class="occasions">
  <div class="occasion honeymoon" role="img" aria-label="Couple relaxing on a beach lounger at a resort"></div>
  <div class="occasion anniversary" role="img" aria-label="Married couple on a seaside terrace"></div>
  <div class="occasion-label" style="left:0">
    <div class="ghost-word">Honeymoons</div>
    <div class="heading" style="position:relative">Honeymoons</div>
    <div class="sub">VIEW PACKAGES</div>
  </div>
  <div class="occasion-label" style="left:600px">
    <div class="ghost-word">Anniversaries</div>
    <div class="heading" style="position:relative">Anniversaries</div>
    <div class="sub">VIEW PACKAGES</div>
  </div>
</section>

<section class="welcome">
  <div class="ghost">Welcome</div>
  <h2 class="heading">Welcome to<br>Harbors and Hammocks Travel Agency</h2>
  <div class="tagline">LOREM IPSUM DOLOR SIT AMET</div>
  <p>Lorem ipsum dolor sit amet, consectetur adipiscing elit, sed do eiusmod tempor incididunt ut labore et dolore magna aliqua. Ut enim ad minim veniam, quis nostrud exercitation ullamco laboris nisi ut aliquip ex ea commodo consequat. Duis aute irure dolor in reprehenderit in voluptate velit esse cillum dolore eu fugiat nulla pariatur. Excepteur sint occaecat cupidatat non proident.</p>
  <span class="btn">Call today for a free consultation!</span>
</section>

<section class="specialties">
  <div class="ghost">We Specialize In</div>
  <h2 class="heading">We Specialize In</h2>
  <div class="spec-card" style="left:88px">
    <div class="photo" style="inset:0;background:linear-gradient(180deg,#7fb0d8,#3c8fb0 55%,#2f6a4a)" role="img" aria-label="Hawaii coastline with city and mountains"></div>
    <svg class="pin" width="28" height="28" viewBox="0 0 28 28"><circle cx="14" cy="14" r="12" fill="none" stroke="#fff" stroke-width="2"/><circle cx="14" cy="14" r="4" fill="#fff"/></svg>
    <div class="label">HAWAII</div>
  </div>
  <div class="spec-card" style="left:434px">
    <div class="photo" style="inset:0;background:linear-gradient(180deg,#f2b07a,#d98a5a 45%,#3a6e86)" role="img" aria-label="European canal city at sunset"></div>
    <svg class="pin" width="28" height="28" viewBox="0 0 28 28"><circle cx="14" cy="14" r="12" fill="none" stroke="#fff" stroke-width="2"/><circle cx="14" cy="14" r="4" fill="#fff"/></svg>
    <div class="label">EUROPE</div>
  </div>
  <div class="spec-card" style="left:780px">
    <div class="photo" style="inset:0;background:linear-gradient(160deg,#3fc2c0,#7fd8cf 50%,#2f8a6a)" role="img" aria-label="Caribbean island with turquoise lagoon"></div>
    <svg class="pin" width="28" height="28" viewBox="0 0 28 28"><circle cx="14" cy="14" r="12" fill="none" stroke="#fff" stroke-width="2"/><circle cx="14" cy="14" r="4" fill="#fff"/></svg>
    <div class="label">CARIBBEAN</div>
  </div>
</section>

<section class="about">
  <div class="photo portrait" role="img" aria-label="Portrait of the agency owner"></div>
  <div class="ghost">About Us</div>
  <div class="about-text">
    <h2 class="heading">About Us</h2>
    <div class="name">Marla Dunbevy</div>
    <div class="role">Agency Owner</div>
    <p>Marla has been traveling full time for the passed two years and has been very passionate about travel from a young age. Marla is dedicated to working closely with clients to book their dream vacation.</p>
    <p style="margin-top:20px">Marla's specializations include honeymoons and anniversaries focusing on travel in Europe, Hawaii and all inclusive resorts in the Caribbean.</p>
  </div>
</section>

<section class="gallery">
  <div class="ghost">Gallery</div>
  <h2 class="heading">Gallery</h2>
  <div class="gallery-grid">
    <div role="img" aria-label="Sunset over the sea with red flowers" style="background:linear-gradient(180deg,#f4a24a,#e76a3a 50%,#2f5d7a)"></div>
    <div role="img" aria-label="Woman lounging in a tropical hammock" style="background:linear-gradient(180deg,#6f9a5a,#c9b08a 60%,#5f8aa0)"></div>
    <div role="img" aria-label="Historic bridge over a river at dusk" style="background:linear-gradient(180deg,#f1b86a,#9a8a7a 55%,#4a5a6a)"></div>
    <div role="img" aria-label="Couple walking along a palm beach" style="background:linear-gradient(180deg,#8cc8e8,#bfe4ee 50%,#e9dcc0)"></div>
    <div role="img" aria-label="Cruise ship on deep blue water" style="background:linear-gradient(180deg,#5fa8dc,#2d6eb0 55%,#14406e)"></div>
    <div role="img" aria-label="Aerial view of a white sand beach" style="background:linear-gradient(160deg,#1fa3a8,#6ad0c8 55%,#f2ead6)"></div>
  </div>
  <span class="btn">View All</span>
</section>

<section class="contact">
  <div class="desk" role="img" aria-label="Travel planning desk with keyboard, map and camera"></div>
  <div class="panel"></div>
  <div class="ghost">Contact</div>
  <h2 class="heading">Contact Us</h2>
  <div class="contact-form">
    <div class="row"><div class="field">Name</div><div class="field">Email</div></div>
    <div class="field">Subject</div>
    <div class="field tall">Message</div>
    <div class="submit">BOOK NOW</div>
  </div>
</section>

<footer class="site-footer">
  <div class="brand"><span class="brand-dot"></span>Harbors and Hammocks</div>
  <div class="contact-line">Email: marla@harborsandhammockstravel.example &nbsp;|&nbsp; Phone number : +1 555 014 2290</div>
  <div class="socials"><span></span><span></span></div>
  <div class="copyright">© 2021 Copyrights The Company Name All Rights Reserved.</div>
</footer>

</body>
</html>
```